Rack Card for Charter Sail Boat business in SF Bay

We are in need of a rack card design to highlight the business to tourists and locals. 2 sided card 3.86" x 8.39" (full bleed)

We are looking for visually appleaing designs on the front and back but a little more detail on the back.

Use the info provided (text and info) on the website to include the 3 key services (Quick, 1/2 day, fullday) and aspects of the boat, location and other key info for customers (not prices). DO NOT INCLUDE ALL THIS TEXT please pick the elements you would like to fit your design and inform the customer as you would like about the business.

I can also provide photos directly from the video if you think those would fit your design. If video doesn't work on this upload you can view it at the website or facebook page (www.fb.com/tidewrenmarinellc)

Target Market(s)

Tourists and locals to san francisco east bay. 25 - 55 years old. Men and women.

Industry/Entity Type

Entertainment

Colors
0455a3
ec1f27
f3f1f8

Requirements
Must have
• Highlight services, key contact information (email, phone, website site), Visual impact
• 2-sided card - 3.86" x 8.39" (98 x 213 mm)
Nice to have
• facebook link, electric engine(green),

```html
<!DOCTYPE html>
<html lang="en">
<head>
<meta charset="utf-8">
<title>Tidewren Marine – East Bay Sailboat Charter Rack Card</title>
<link href="https://fonts.googleapis.com/css2?family=Lobster&family=Oswald:wght@500;600&family=Roboto+Condensed:wght@400;500;700&display=swap" rel="stylesheet">
<style>
  :root {
    --brand-blue: #0455a3;
    --deep-blue: #0b3a78;
    --navy: #0a2a5a;
    --brand-red: #ec1f27;
    --band-red: #d8282e;
    --paper: #f3f1f8;
    --white: #ffffff;
    --stage: #d9d8dc;
  }
  * { box-sizing: border-box; margin: 0; padding: 0; }
  html, body { width: 1200px; height: 977px; overflow: hidden; }
  body {
    background: var(--stage);
    font-family: "Roboto Condensed", Arial, sans-serif;
    position: relative;
  }
  .card {
    position: absolute;
    top: 48px;
    width: 405px;
    height: 880px;
    overflow: hidden;
    box-shadow: 0 6px 18px rgba(0,0,0,.25);
  }
  .card--front { left: 160px; }
  .card--back { left: 635px; background: var(--deep-blue); }

  /* FRONT */
  .front-photo {
    position: absolute; inset: 0;
    background: linear-gradient(180deg, #5f95d4 0%, #7eaadc 30%, #9fb9cf 45%, #6f8fae 52%, #4a6f96 62%, #2f5889 80%, #1f4b86 100%);
  }
  .brand {
    position: absolute; top: 52px; left: 0; right: 0;
    display: flex; align-items: center; justify-content: center; gap: 10px;
    color: var(--white);
    font-family: "Roboto Condensed", Arial, sans-serif;
    font-weight: 500; font-size: 26px; letter-spacing: 1px;
  }
  .brand__dot { width: 34px; height: 34px; border-radius: 50%; background: var(--white); }
  .headline {
    position: absolute; top: 170px; left: 20px; width: 370px;
    text-align: center;
    transform: rotate(-8deg);
  }
  .headline__kicker {
    font-family: "Oswald", Arial, sans-serif; font-weight: 600;
    font-size: 40px; color: var(--white); letter-spacing: .5px; line-height: 1;
    text-shadow: 0 2px 4px rgba(0,0,0,.3);
  }
  .headline__main {
    font-family: "Lobster", cursive; font-size: 88px; line-height: 1;
    color: var(--brand-blue);
    text-shadow: 3px 3px 0 var(--white), -3px -3px 0 var(--white), 3px -3px 0 var(--white), -3px 3px 0 var(--white), 0 6px 8px rgba(0,0,0,.35);
  }
  .headline__sub {
    font-family: "Lobster", cursive; font-size: 48px; line-height: 1;
    color: var(--brand-red); margin: -14px 0 0 150px;
    text-shadow: 2px 2px 0 var(--white), -2px -2px 0 var(--white), 2px -2px 0 var(--white), -2px 2px 0 var(--white);
  }
  .route-maps {
    position: absolute; right: 24px; bottom: 120px;
    width: 200px; height: 190px;
    background: linear-gradient(135deg, #e6eef5 0%, #a9cbe6 45%, #dfe8d5 100%);
    transform: rotate(-8deg);
    border: 6px solid var(--white);
  }
  .services {
    position: absolute; left: 30px; bottom: 56px;
    transform: rotate(-8deg); transform-origin: left bottom;
  }
  .services__title {
    font-family: "Lobster", cursive; font-size: 32px; color: var(--brand-red);
    text-shadow: 2px 2px 0 var(--white), -2px -2px 0 var(--white), 2px -2px 0 var(--white), -2px 2px 0 var(--white);
    margin-bottom: 6px;
  }
  .services__list { list-style: none; }
  .services__item {
    display: flex; align-items: center; gap: 8px;
    font-family: "Oswald", Arial, sans-serif; font-weight: 500;
    font-size: 16px; color: var(--white); line-height: 1.55;
  }
  .services__item svg { width: 13px; height: 13px; }

  /* BACK */
  .back-top {
    position: absolute; top: 0; left: 0; right: 0; height: 430px;
    background: linear-gradient(180deg, var(--brand-blue) 0%, #0d4d96 100%);
  }
  .back-skyline {
    position: absolute; top: 250px; left: 0; right: 0; height: 140px;
    background: linear-gradient(180deg, rgba(10,42,90,0) 0%, rgba(10,42,90,.55) 60%, rgba(10,42,90,.3) 100%);
  }
  .intro {
    position: absolute; top: 22px; left: 22px; right: 22px;
    color: var(--white); font-size: 12.2px; line-height: 1.5; text-align: center;
  }
  .intro p + p { margin-top: 14px; }
  .safety {
    position: absolute; top: 390px; left: 0; right: 0; height: 290px;
    background: var(--band-red);
    clip-path: polygon(0 0, 100% 0, 100% 86%, 50% 100%, 0 86%);
    border-top: 2px solid var(--white);
  }
  .safety__title {
    position: absolute; top: 374px; left: 0; right: 0; text-align: center;
    font-family: "Lobster", cursive; font-size: 36px; color: var(--brand-blue);
    text-shadow: 2px 2px 0 var(--white), -2px -2px 0 var(--white), 2px -2px 0 var(--white), -2px 2px 0 var(--white);
  }
  .safety__text {
    position: absolute; top: 428px; left: 20px; right: 20px;
    color: var(--white); font-size: 12.2px; line-height: 1.5; text-align: center;
  }
  .back-bottom {
    position: absolute; top: 640px; left: 0; right: 0; bottom: 0;
    background: linear-gradient(180deg, var(--deep-blue), var(--navy));
    z-index: -0;
  }
  .contact {
    position: absolute; top: 700px; left: 0; right: 0; text-align: center; color: var(--white);
  }
  .contact__brand {
    display: flex; align-items: center; justify-content: center; gap: 8px;
    font-weight: 500; font-size: 15px; letter-spacing: .5px; margin-bottom: 10px;
  }
  .contact__brand span { width: 16px; height: 16px; border-radius: 50%; background: var(--white); }
  .contact__cta { font-family: "Lobster", cursive; font-size: 30px; line-height: 1.2; }
  .contact__phone { font-weight: 700; font-size: 30px; line-height: 1.3; letter-spacing: .3px; }
  .contact__line { font-size: 19px; line-height: 1.3; }
</style>
</head>
<body>

<article class="card card--front">
  <div class="front-photo" role="img" aria-label="Photo of a two-masted sailboat with white sails cruising on San Francisco Bay under a blue sky"></div>
  <div class="brand"><span class="brand__dot"></span>Tidewren Marine</div>
  <h1 class="headline">
    <div class="headline__kicker">ULTIMATE EAST BAY</div>
    <div class="headline__main">Sailboat</div>
    <div class="headline__sub">Charter</div>
  </h1>
  <div class="route-maps" role="img" aria-label="Three maps of San Francisco Bay showing dotted sailing routes"></div>
  <section class="services">
    <h2 class="services__title">Over Services</h2>
    <ul class="services__list">
      <li class="services__item"><svg viewBox="0 0 14 14"><circle cx="7" cy="7" r="7" fill="#fff"/><path d="M4 7h5M7 4.5 9.5 7 7 9.5" stroke="#0455a3" stroke-width="1.8" fill="none"/></svg>QUICK BLAST</li>
      <li class="services__item"><svg viewBox="0 0 14 14"><circle cx="7" cy="7" r="7" fill="#fff"/><path d="M4 7h5M7 4.5 9.5 7 7 9.5" stroke="#0455a3" stroke-width="1.8" fill="none"/></svg>1/2 DAY FUN</li>
      <li class="services__item"><svg viewBox="0 0 14 14"><circle cx="7" cy="7" r="7" fill="#fff"/><path d="M4 7h5M7 4.5 9.5 7 7 9.5" stroke="#0455a3" stroke-width="1.8" fill="none"/></svg>FULL DAY ADVENTURE</li>
    </ul>
  </section>
</article>

<article class="card card--back">
  <div class="back-bottom"></div>
  <div class="back-top"></div>
  <div class="back-skyline" role="img" aria-label="Faint San Francisco skyline seen across the water"></div>
  <div class="intro">
    <p>Come enjoy an amazing experience aboard Tidewren and view San Francisco and the rest of the bay as so few are able to do. Tidewren is a supreme blue-water cruising boat with all the modern safety, comfort and entertainment equipment you would expect. Your time aboard Tidewren is yours to enjoy and direct as you wish while we show you San Francisco Bay, the Golden Gate Bridge, Alcatraz, Treasure and Angel Islands and so much more.</p>
    <p>Tidewren is located at the Berkeley Marina and perfectly placed to take advantage of the vast and beautiful Bay. Those that live or visit the East Bay or the Central Valley can easily reach the marina and parking is no problem. Within a few minutes of arriving on the boat you can be "shooting the slot" and experiencing the thrill of dropping the rail into the water or warming yourself with refreshment in the protection of Angel Island.</p>
    <p>Come join us and share the wonders around San Francisco Bay with your friends and family. We love to show families how to sail and have great fun on the water while staying safe.</p>
  </div>
  <div class="safety"></div>
  <h2 class="safety__title">Safety Features</h2>
  <p class="safety__text">The safety of everyone aboard Tidewren is paramount to our business and your enjoyment. We carry aboard everything to make your time aboard safe. Life preservers are of course provided and available for all including kids sizes. We carry the USCG bulky ones as well as modern self inflating slim comfortable life jackets. Also loaded for every trip is a complete first aid kit, AED, EPIRB, and many other safety items that we are fully trained to use but hope we never have to. Children 5 and over are happily encouraged to come along, though children younger are discouraged as parents spend more time keeping their little ones safe than enjoying the sail. Tidewren is a center cockpited vessel which means kids can be positioned safely where the boat moves least but still exciting - plus we have harnesses available to ensure they don't move out of the safe zone if you need.</p>
  <div class="contact">
    <div class="contact__brand"><span></span>Tidewren Marine</div>
    <div class="contact__cta">Call Us Today</div>
    <div class="contact__phone">+1 (555) 014 SAIL (7245)</div>
    <div class="contact__line">Bookings@TidewrenMarine.com</div>
    <div class="contact__line">www.fb.com/tidewrenmarinellc</div>
  </div>
</article>

</body>
</html>
```